Zolvana Stationary and Branding Documents

Corporate Identity Branding stationary needed for IT Recruiting Firm.

I already have a Logo, business cards and website. I need to get designs completed for the remaining corporate identity documents.

The documentation should use similar colors as my website and business card. The designs should modern and clean.

http://zolvanaworks.example/

Target Market(s)

Information Technology Industry

Industry/Entity Type

Information Technology

Colors
3377b5
0255a3
fbee3e
f78f20
f37122
33a6d7
000000
0592cd

Requirements
Must have
• Letter Head
• Folder Design
• PowerPoint Design
• Invoice
• Envelope
Nice to have
• Proposal
• Flyer
• Brochure
Should not have
• Logo
• Business Cards
• Website

```html
<!DOCTYPE html>
<html lang="en">
<head>
<meta charset="utf-8">
<title>Zolvana Stationery Suite</title>
<link href="https://fonts.googleapis.com/css2?family=Montserrat:wght@400;500;600;700&family=Open+Sans:wght@400;600&family=Courier+Prime&display=swap" rel="stylesheet">
<style>
:root{
  --blue:#0a55a8;
  --blue-dark:#08458c;
  --navy:#1f3f8f;
  --ink:#2b2b2b;
  --dark:#2e2e2e;
  --orange:#f37122;
  --amber:#f78f20;
  --bg:#c9ccd1;
  --paper:#ffffff;
  --text:#333;
}
*{box-sizing:border-box;margin:0;padding:0}
html,body{width:1200px;height:1200px;overflow:hidden}
body{background:linear-gradient(135deg,#d3d5d9,#c3c6cb);font-family:"Open Sans",sans-serif;color:var(--text);position:relative}
.sheet{position:absolute;background:var(--paper);overflow:hidden;box-shadow:0 3px 8px rgba(0,0,0,.22)}
.band{position:absolute;left:0;bottom:0;width:100%}
.band .dk{fill:var(--dark)}
.band .bl{fill:var(--blue)}
.brand{font-family:"Montserrat",sans-serif;font-weight:500;color:var(--blue);letter-spacing:.5px;display:flex;align-items:center;gap:4px;line-height:1}
.brand .dot{width:.28em;height:.28em;background:var(--orange)}
.brand.white{color:#fff}
.tiny{font-size:3.2px;line-height:4.4px;color:#555}
.h{font-family:"Montserrat",sans-serif;font-weight:600;color:var(--blue);text-transform:uppercase}
.photo{position:absolute}
.photo.tech{background:radial-gradient(circle at 55% 50%,#cfe6f7 0,#5f8fbf 30%,#27415f 70%,#1b2a3c 100%)}
.photo.desk{background:linear-gradient(160deg,#f1f1f1,#b9bcc1 60%,#6d7075)}
.photo.team{background:linear-gradient(135deg,#e9eef2,#9fb1c1)}
.contacts{position:absolute;display:flex;gap:10px;font-size:3px;color:#fff;align-items:center}
.contacts span::before{content:"";display:inline-block;width:3px;height:3px;border-radius:50%;background:#fff;margin-right:2px;vertical-align:middle}
.ticks{font-size:3px;color:#444;line-height:5px}
.ticks li{list-style:none}
.ticks li::before{content:"";display:inline-block;width:2.5px;height:2.5px;background:var(--orange);margin-right:3px}
.mono{font-family:"Courier Prime",monospace}
.dots3{display:flex;gap:2px;justify-content:center;margin:2px 0}
.dots3 i{width:3px;height:3px;background:var(--orange)}
.panel{position:absolute;top:0;height:100%;overflow:hidden}
</style>
</head>
<body>

<!-- Folder -->
<section class="sheet folder" style="left:72px;top:138px;width:428px;height:294px">
  <div style="position:absolute;left:0;top:0;width:214px;height:100%;background:linear-gradient(135deg,var(--blue),var(--blue-dark))"></div>
  <svg class="band" viewBox="0 0 214 100" preserveAspectRatio="none" style="left:214px;width:214px;height:100px">
    <polygon class="dk" points="0,0 214,20 214,100 0,100"/>
    <polygon class="bl" points="0,36 214,-4 214,100 0,100"/>
  </svg>
  <div class="brand" style="position:absolute;left:266px;top:124px;font-size:27px">Zolvana<i class="dot"></i></div>
  <div class="contacts" style="left:62px;top:278px"><span>5550142870</span><span>info@zolvanaworks.example</span><span>www.zolvanaworks.example</span></div>
</section>

<!-- Letterhead -->
<section class="sheet letterhead" style="left:517px;top:186px;width:209px;height:296px">
  <div class="brand" style="position:absolute;left:70px;top:18px;font-size:16px">Zolvana<i class="dot"></i></div>
  <div class="tiny" style="position:absolute;top:40px;width:100%;text-align:center;font-size:2.6px">Two Harbor Plaza 410 9th Street NE</div>
  <div class="tiny" style="position:absolute;left:31px;top:56px;font-weight:600;color:#222">Dear, Sir<br>Designation<br>Company Name</div>
  <div class="tiny" style="position:absolute;right:30px;top:56px;font-weight:600;color:#222">DATE:1/5/2018</div>
  <div class="tiny" style="position:absolute;left:31px;top:75px;width:148px;font-size:2.6px;line-height:3.6px">
    <p style="margin-bottom:6px">We place skilled technology people with companies that need them. Our team reviews each candidate with care, tests real skills, and prepares every person for the role ahead. We work closely with clients to learn their needs and to match talent that will stay and grow with the business over many years.</p>
    <p style="margin-bottom:6px">We place skilled technology people with companies that need them. Our team reviews each candidate with care, tests real skills, and prepares every person for the role ahead. We work closely with clients to learn their needs and to match talent that will stay and grow.</p>
    <p style="margin-bottom:6px">We place skilled technology people with companies that need them. Our team reviews each candidate with care, tests real skills, and prepares every person for the role ahead. We work closely with clients to learn their needs and to match talent that will stay and grow.</p>
    <p>We place skilled technology people with companies that need them. Our team reviews each candidate with care, tests real skills, and prepares every person for the role ahead.</p>
  </div>
  <div class="tiny" style="position:absolute;right:30px;top:216px;font-weight:600;color:#222;text-align:right">YOUR NAME<br><span style="font-weight:400">Designation</span></div>
  <svg class="band" viewBox="0 0 209 60" preserveAspectRatio="none" style="height:60px">
    <polygon class="dk" points="0,14 209,30 209,60 0,60"/>
    <polygon class="bl" points="0,38 209,6 209,60 0,60"/>
  </svg>
  <div class="contacts" style="left:50px;top:285px;font-size:2.4px"><span>5550142870</span><span>info@zolvanaworks.example</span><span>www.zolvanaworks.example</span></div>
</section>

<!-- Presentation -->
<section class="sheet presentation" style="left:750px;top:238px;width:260px;height:198px">
  <div class="brand" style="position:absolute;left:18px;top:18px;font-size:17px">Zolvana<i class="dot"></i></div>
  <div style="position:absolute;right:19px;top:20px;text-align:right;font-family:Montserrat,sans-serif">
    <div style="font-size:7px;color:#333">PRESENTATION</div>
    <div style="font-size:14px;font-weight:700;color:var(--blue);line-height:1">TEMPLATE</div>
  </div>
  <div style="position:absolute;left:18px;top:64px;font-family:Montserrat,sans-serif;line-height:1">
    <div style="font-size:12px;color:#222">TEXT</div>
    <div style="font-size:15px;font-weight:700;color:var(--blue)">HEADLINE</div>
  </div>
  <p class="tiny" style="position:absolute;left:18px;top:98px;width:82px;font-size:2.8px;line-height:3.4px;color:#222">We match proven technology talent with firms that want steady growth. Every hire is screened, trained and supported from the first day onward.</p>
  <svg class="band" viewBox="0 0 260 62" preserveAspectRatio="none" style="height:62px">
    <polygon class="dk" points="0,6 260,24 260,62 0,62"/>
    <polygon class="bl" points="0,36 260,0 260,62 0,62"/>
  </svg>
</section>

<!-- Flyer -->
<section class="sheet flyer" style="left:56px;top:502px;width:212px;height:298px">
  <div class="photo tech" role="img" aria-label="Business people and laptop with network globe graphics" style="left:0;top:0;width:100%;height:76px;clip-path:polygon(0 0,100% 0,100% 78%,0 100%)"></div>
  <div class="brand" style="position:absolute;left:67px;top:70px;font-size:17px">Zolvana<i class="dot"></i></div>
  <div style="position:absolute;left:19px;top:100px;width:176px">
    <div class="h" style="font-size:5.5px">About Zolvana</div>
    <p class="tiny" style="font-size:3px;line-height:3.8px;color:#222">Zolvana is not a standard recruitment firm. We are veteran IT professionals who know the industry and what it takes to succeed. We work with select candidates and give them training and a plan to move up.</p>
    <div class="h" style="font-size:5.5px;margin-top:6px">What we do</div>
    <p class="tiny" style="font-size:3px;line-height:3.8px;color:#222"><b style="color:var(--blue)">IT RECRUITING</b> Zolvana is a premier source for elite IT talent. We choose the best and make them better.</p>
    <p class="tiny" style="font-size:3px;line-height:3.8px;color:#222;margin-top:2px"><b style="color:var(--blue)">Career Mentoring</b> Zolvana uses real scenario training so each candidate can apply skills at work.</p>
  </div>
  <div style="position:absolute;left:19px;top:184px;width:80px">
    <div class="h" style="font-size:5px">The Zolvana Advantage</div>
    <div style="font-size:3px;color:var(--blue);font-weight:600;margin-bottom:3px">Zolvana is a better path to IT talent</div>
    <ul class="ticks"><li>We believe talent is everything</li><li>We're in it for the long run</li><li>We live what we do</li><li>We love what we do</li></ul>
  </div>
  <div style="position:absolute;left:123px;top:184px;width:74px">
    <div class="h" style="font-size:5px;line-height:6px">Zolvana helps smart companies succeed faster</div>
    <p class="tiny" style="font-size:2.8px;line-height:3.4px;color:#222">With Zolvana there's no guesswork; you get a candidate ready for the job.</p>
    <ul class="ticks" style="margin-top:3px"><li>Fill Positions Quickly</li><li>Improve productivity and value</li></ul>
  </div>
  <svg class="band" viewBox="0 0 212 64" preserveAspectRatio="none" style="height:64px">
    <polygon class="dk" points="0,16 212,30 212,64 0,64"/>
    <polygon class="bl" points="0,40 212,6 212,64 0,64"/>
  </svg>
  <div class="contacts" style="left:10px;top:285px;font-size:2.5px;gap:6px"><span>5550142870</span><span>info@zolvanaworks.example</span><span>Two Harbor Plaza 410 9th St NE</span><span>www.zolvanaworks.example</span></div>
</section>

<!-- Proposal -->
<section class="sheet proposal" style="left:288px;top:502px;width:212px;height:298px">
  <div class="brand" style="position:absolute;left:21px;top:24px;font-size:15px">Zolvana<i class="dot"></i></div>
  <div class="tiny" style="position:absolute;left:24px;top:166px;font-size:2.8px;line-height:7px;color:#222">NAME OF PROPONENT<br>ADDRESS<br>CITY/TOWN<br>STATE/PROVINCE<br>ZIP/POSTAL CODE<br>COUNTRY IF APPLICABLE</div>
  <svg class="band" viewBox="0 0 212 100" preserveAspectRatio="none" style="height:100px">
    <polygon class="dk" points="0,10 212,26 212,100 0,100"/>
    <polygon class="bl" points="0,38 212,0 212,100 0,100"/>
  </svg>
  <div style="position:absolute;right:17px;bottom:16px;text-align:right;color:#fff;font-family:Montserrat,sans-serif">
    <div style="font-size:4px;font-weight:600">ZOLVANA PROJECTS</div>
    <div style="font-size:16px;font-weight:700;line-height:1.1">PROPOSAL</div>
    <div style="font-size:4px">SPECIFY PROJECT FOCUS</div>
  </div>
</section>

<!-- Invoice -->
<section class="sheet invoice" style="left:517px;top:502px;width:209px;height:296px">
  <div class="brand" style="position:absolute;left:70px;top:20px;font-size:16px">Zolvana<i class="dot"></i></div>
  <div class="h" style="position:absolute;width:100%;top:52px;text-align:center;font-size:13px;font-weight:700">Invoice</div>
  <div class="mono tiny" style="position:absolute;left:24px;top:77px;font-size:3.4px;color:#222">Two Harbor Plaza 410<br>9th Street NE<br>info@zolvanaworks.example<br>5550142870<br>www.zolvanaworks.example</div>
  <div class="mono tiny" style="position:absolute;right:24px;top:77px;font-size:3.4px;color:#222">INVOICE # &nbsp;&nbsp;12121<br>DATE &nbsp;&nbsp;&nbsp;10/01/2018</div>
  <table class="mono" style="position:absolute;left:24px;top:111px;width:162px;border-collapse:collapse;font-size:3.4px;color:#222">
    <tr style="background:var(--amber);color:#222"><td style="padding:1px 2px">QTY</td><td>PRODUCT DESCRIPTION</td><td>PRICE</td><td style="text-align:right;padding-right:2px">TOTAL</td></tr>
    <tr style="border:.5px solid #888"><td style="padding:2.5px 2px">1</td><td>PROJECT Title 1</td><td>$ 50.00</td><td style="text-align:right;padding-right:2px">$250.00</td></tr>
    <tr style="border:.5px solid #888"><td style="padding:2.5px 2px">2</td><td>PROJECT Title 2</td><td>$ 50.00</td><td style="text-align:right;padding-right:2px">$250.00</td></tr>
    <tr style="border:.5px solid #888"><td style="padding:2.5px 2px">3</td><td>PROJECT Title 3</td><td>$ 50.00</td><td style="text-align:right;padding-right:2px">$250.00</td></tr>
    <tr style="border:.5px solid #888"><td style="padding:2.5px 2px">4</td><td>PROJECT Title 4</td><td>$ 50.00</td><td style="text-align:right;padding-right:2px">$250.00</td></tr>
    <tr style="border:.5px solid #888"><td style="padding:2.5px 2px">5</td><td>PROJECT Title 5</td><td>$ 50.00</td><td style="text-align:right;padding-right:2px">$250.00</td></tr>
  </table>
  <div class="mono tiny" style="position:absolute;left:24px;top:179px;font-size:2.8px;color:#222">EMAIL:<br>Bank:<br>Bank Sort Code:<br>Account Number:<br>Payment Reference:</div>
  <div class="mono tiny" style="position:absolute;right:24px;top:179px;font-size:2.8px;color:#222;text-align:right">Subtotal &nbsp;$4,250.00<br>Tax Rate &nbsp;&nbsp;0.00%<br><br><span style="font-size:3.6px">TOTAL &nbsp;&nbsp;$415.00</span></div>
  <div class="mono tiny" style="position:absolute;left:24px;top:220px;font-size:2.6px;color:#222">THANK YOU FOR YOUR BUSINESS<br>Payment is due within 7 days of receipt.</div>
  <svg class="band" viewBox="0 0 209 56" preserveAspectRatio="none" style="height:56px">
    <polygon class="dk" points="0,10 209,28 209,56 0,56"/>
    <polygon class="bl" points="0,40 209,6 209,56 0,56"/>
  </svg>
</section>

<!-- Brochure outside -->
<section class="sheet brochure-out" style="left:750px;top:464px;width:418px;height:294px">
  <div class="panel" style="left:0;width:140px">
    <div class="h" style="position:absolute;top:18px;width:100%;text-align:center;font-size:8px">About Zolvana</div>
    <div class="dots3" style="position:absolute;top:30px;width:100%"><i></i><i></i><i></i></div>
    <p class="tiny" style="position:absolute;left:14px;top:40px;width:112px;font-size:3.8px;line-height:4.8px;color:#222">Zolvana is not a standard recruitment firm. We are veteran IT professionals who know the industry and what it takes to succeed. We work with select candidates and give them training and a plan to move up, not one rung but all the way to your career goals.</p>
    <div class="h" style="position:absolute;top:104px;width:100%;text-align:center;font-size:8px">Join the Elite</div>
    <div class="dots3" style="position:absolute;top:116px;width:100%"><i></i><i></i><i></i></div>
    <p class="tiny" style="position:absolute;left:14px;top:126px;width:112px;font-size:3.8px;line-height:4.8px;color:#222">Elite IT talent is no accident. It takes drive, smarts and smart career counseling. Do you have what it takes? We provide mentoring and counsel and we'll stay with you through your career.</p>
    <svg class="band" viewBox="0 0 140 120" preserveAspectRatio="none" style="height:120px">
      <polygon class="dk" points="0,0 140,10 140,120 0,120"/>
      <polygon class="bl" points="0,28 140,12 140,120 0,120"/>
    </svg>
    <div class="brand white" style="position:absolute;top:222px;width:100%;justify-content:center;font-size:16px">Zolvana<i class="dot"></i></div>
    <div style="position:absolute;top:258px;width:100%;text-align:center;color:#fff;font-family:Montserrat,sans-serif;font-size:8px;font-weight:600">JOIN US</div>
  </div>
  <div class="photo tech" role="img" aria-label="Hand holding a phone with network globe and connected people icons" style="left:140px;top:0;width:278px;height:170px"></div>
  <svg class="band" viewBox="0 0 278 150" preserveAspectRatio="none" style="left:140px;width:278px;height:150px">
    <polygon class="dk" points="0,0 278,30 278,150 0,150"/>
    <polygon class="bl" points="0,40 278,-8 278,150 0,150"/>
  </svg>
  <div style="position:absolute;left:152px;top:204px;color:#fff;font-size:4.2px;line-height:14px">
    <div>&#9990; 5550142870</div><div>&#9993; info@zolvanaworks.example</div><div>&#9679; Two Harbor Plaza 410 9th Street NE</div><div>&#9679; www.zolvanaworks.example</div>
  </div>
  <div style="position:absolute;left:298px;top:205px;width:100px;height:52px;background:#fff;border-radius:5px;display:flex;align-items:center;justify-content:center">
    <div class="brand" style="font-size:15px">Zolvana<i class="dot"></i></div>
  </div>
</section>

<!-- Envelope back -->
<section class="sheet envelope-back" style="left:58px;top:824px;width:324px;height:160px">
  <div style="position:absolute;left:0;top:0;width:100%;height:50px;background:var(--blue);border-radius:0 0 8px 8px"></div>
  <div style="position:absolute;left:135px;top:17px;display:flex;gap:9px"><i style="width:11px;height:14px;background:#2f70bd;display:block"></i><i style="width:11px;height:14px;background:#2f70bd;display:block"></i><i style="width:11px;height:14px;background:#2f70bd;display:block"></i></div>
</section>

<!-- Envelope front -->
<section class="sheet envelope-front" style="left:405px;top:824px;width:323px;height:160px">
  <div style="position:absolute;left:24px;top:60px;width:108px;height:54px;background:var(--blue);border-radius:9px"></div>
  <div class="brand" style="position:absolute;right:18px;top:26px;font-size:19px">Zolvana<i class="dot"></i></div>
  <div style="position:absolute;right:18px;top:106px;text-align:right;font-size:5.8px;line-height:8px;color:#222">5550142870<br>info@zolvanaworks.example<br>www.zolvanaworks.example<br>Two Harbor Plaza 410 9th Street NE</div>
</section>

<!-- Brochure inside -->
<section class="sheet brochure-in" style="left:750px;top:782px;width:418px;height:294px">
  <div class="panel" style="left:0;width:140px">
    <svg viewBox="0 0 140 40" preserveAspectRatio="none" style="position:absolute;top:0;left:0;width:140px;height:40px">
      <polygon fill="var(--dark)" points="0,0 140,0 140,6 0,30"/>
    </svg>
    <div class="h" style="position:absolute;top:46px;width:100%;text-align:center;font-size:8px">What we do</div>
    <div class="dots3" style="position:absolute;top:58px;width:100%"><i></i><i></i><i></i></div>
    <div class="h" style="position:absolute;left:14px;top:76px;font-size:8px">IT Recruiting</div>
    <p class="tiny" style="position:absolute;left:14px;top:88px;width:114px;font-size:3.8px;line-height:4.8px;color:#222">Zolvana is the premier source for elite IT talent. We choose the best and make them better. We believe in the personal touch; at Zolvana, you are family.</p>
    <div class="h" style="position:absolute;left:14px;top:130px;font-size:8px">Career Mentoring</div>
    <p class="tiny" style="position:absolute;left:14px;top:142px;width:114px;font-size:3.8px;line-height:4.8px;color:#222">Zolvana uses scenario based training so each candidate has the technical skills and ability to apply those skills in a real business setting.</p>
    <div class="photo desk" role="img" aria-label="Hands typing on a laptop keyboard" style="left:0;top:180px;width:140px;height:114px"></div>
  </div>
  <div class="panel" style="left:140px;width:140px">
    <div class="dots3" style="position:absolute;top:30px;width:100%"><i></i><i></i><i></i></div>
    <div class="h" style="position:absolute;top:40px;width:100%;text-align:center;font-size:7.5px">The Zolvana <span style="color:var(--orange)">Advantage</span></div>
    <div class="tiny" style="position:absolute;top:52px;width:100%;text-align:center;font-size:3.2px">Zolvana is a better path to IT talent</div>
    <div class="photo team" role="img" aria-label="Team meeting around a table" style="left:16px;top:62px;width:50px;height:30px"></div>
    <p class="tiny" style="position:absolute;left:70px;top:64px;width:56px;font-size:3px;line-height:3.8px;color:#222"><b style="color:var(--blue)">WE BELIEVE TALENT IS EVERYTHING</b><br>Technology is an ever changing field, but one thing remains.</p>
    <p class="tiny" style="position:absolute;left:16px;top:94px;width:110px;font-size:3px;line-height:3.8px;color:#222">Great talent is what makes a company succeed, so we work only with elite talent.</p>
    <p class="tiny" style="position:absolute;left:16px;top:122px;width:56px;font-size:3px;line-height:3.8px;color:#222"><b style="color:var(--blue)">WE'RE IN IT FOR THE LONG RUN</b><br>Zolvana is not a sales oriented firm that lives or dies on volume.</p>
    <div class="photo team" role="img" aria-label="Colleagues shaking hands in an office" style="left:76px;top:120px;width:50px;height:30px"></div>
    <p class="tiny" style="position:absolute;left:16px;top:152px;width:110px;font-size:3px;line-height:3.8px;color:#222">We develop a select group of elite talent who will add value for years to come.</p>
    <div class="photo team" role="img" aria-label="Presenter at a whiteboard with colleagues" style="left:16px;top:180px;width:50px;height:30px"></div>
    <p class="tiny" style="position:absolute;left:70px;top:180px;width:56px;font-size:3px;line-height:3.8px;color:#222"><b style="color:var(--blue)">WE LIVE WHAT WE DO</b><br>When we provide IT training and career advice, we know exactly what's needed.</p>
    <p class="tiny" style="position:absolute;left:16px;top:212px;width:110px;font-size:3px;line-height:3.8px;color:#222">We have been the talent ourselves and hired hundreds of people.</p>
    <p class="tiny" style="position:absolute;left:16px;top:232px;width:56px;font-size:3px;line-height:3.8px;color:#222"><b style="color:var(--blue)">WE LOVE WHAT WE DO</b><br>The IT business has been very good to us, and we want to return the favor.</p>
    <div class="photo team" role="img" aria-label="Business people working at laptops" style="left:76px;top:236px;width:50px;height:30px"></div>
    <p class="tiny" style="position:absolute;left:16px;top:268px;width:110px;font-size:3px;line-height:3.8px;color:#222">We focus on what makes IT great: skilled, driven people.</p>
  </div>
  <div class="panel" style="left:280px;width:138px">
    <div class="dots3" style="position:absolute;top:30px;width:100%"><i></i><i></i><i></i></div>
    <div class="h" style="position:absolute;top:40px;width:100%;text-align:center;font-size:8px">Who we are</div>
    <div style="position:absolute;left:14px;top:62px;font-family:Montserrat,sans-serif;font-size:7px;font-weight:600;color:var(--blue)">Zolvana for Elite Candidates</div>
    <p class="tiny" style="position:absolute;left:14px;top:74px;width:112px;font-size:3.4px;line-height:4.4px;color:#222">Zolvana is not a standard recruitment firm. We are veteran IT professionals who know the industry and what it takes to succeed. We give select candidates training and a plan to move up all the way.</p>
    <div style="position:absolute;left:14px;top:122px;font-family:Montserrat,sans-serif;font-size:7px;font-weight:600;color:var(--blue)">Zolvana for Elite Companies</div>
    <p class="tiny" style="position:absolute;left:14px;top:134px;width:112px;font-size:3.4px;line-height:4.4px;color:#222">You'll have value from day one. Each candidate is already vetted and trained for your opening, and that value keeps growing as they build skills every day.</p>
    <div class="photo tech" role="img" aria-label="Hand holding a glowing globe with network lines" style="left:0;top:184px;width:138px;height:86px"></div>
    <div style="position:absolute;left:0;bottom:0;width:100%;height:24px;background:var(--blue)"></div>
  </div>
</section>

</body>
</html>
```